Maple Bus Card

i own a building in the bronx ny - its called "Maple 7 on 2 HDFC"i want a classy logo / business card - nothing too religuous but it is like a family there - its a large apartment building - colors i like dark red, black, medium shade of gray also reg business card stuff tel # 914-555-0173 address 4738 Larkwell Ave Harlow Falls NY 12987 Email fijosh@aol.comslogan - " Together we are home "i can send u a picture of the building for the backside

```html
<!DOCTYPE html>
<html lang="en">
<head>
<meta charset="utf-8">
<title>Maple 7 on 2 HDFC — Business Card</title>
<link rel="stylesheet" href="https://fonts.googleapis.com/css2?family=Montserrat:wght@700&family=Open+Sans:wght@400;600&display=swap">
<style>
  :root {
    --page: #4a4a4a;
    --card: #2b2b2b;
    --band: #7b7b7b;
    --gold: #f2b01e;
    --text: #d9d9d9;
    --rule: #6d6d6d;
    --brick: #7a3a2e;
    --leaf: #3f5a2a;
  }
  * { margin: 0; padding: 0; box-sizing: border-box; }
  html, body { width: 1200px; height: 896px; overflow: hidden; }
  body {
    background: var(--page);
    display: flex;
    flex-direction: column;
    align-items: center;
    justify-content: center;
    gap: 32px;
    font-family: "Open Sans", Arial, sans-serif;
  }
  .card {
    position: relative;
    width: 700px;
    height: 400px;
    background: var(--card);
    overflow: hidden;
    box-shadow: 0 10px 24px rgba(0,0,0,.45);
  }
  .card-front .band {
    position: absolute;
    left: 0; right: 0; bottom: 0;
    height: 118px;
    background: var(--band);
  }
  .contact {
    position: absolute;
    left: 48px; top: 92px;
  }
  .person-name {
    font-family: "Montserrat", Arial, sans-serif;
    font-weight: 700;
    font-size: 25px;
    color: var(--gold);
    letter-spacing: .5px;
  }
  .person-title {
    font-size: 17px;
    color: var(--text);
    margin: 2px 0 14px;
  }
  .contact-line {
    display: flex;
    align-items: center;
    gap: 10px;
    font-size: 17px;
    color: var(--text);
    line-height: 26px;
  }
  .contact-line svg { width: 16px; height: 16px; flex: none; }
  .divider {
    position: absolute;
    left: 300px; top: 118px;
    width: 200px; height: 1px;
    background: var(--rule);
  }
  .brand {
    position: absolute;
    right: 48px; top: 168px;
    text-align: right;
  }
  .brand-mark {
    display: flex;
    align-items: center;
    justify-content: flex-end;
    gap: 12px;
  }
  .brand-dot {
    width: 16px; height: 16px;
    border-radius: 50%;
    background: var(--gold);
  }
  .brand-name {
    font-family: "Montserrat", Arial, sans-serif;
    font-weight: 700;
    font-size: 28px;
    color: var(--gold);
    letter-spacing: .5px;
  }
  .address {
    margin-top: 10px;
    font-size: 17px;
    line-height: 23px;
    color: var(--text);
  }
  .slogan {
    position: absolute;
    left: 48px; bottom: 44px;
    font-family: "Montserrat", Arial, sans-serif;
    font-weight: 700;
    font-size: 21px;
    color: var(--gold);
    letter-spacing: .5px;
  }
  .building-photo {
    position: absolute;
    inset: 0;
    background:
      linear-gradient(180deg, var(--leaf) 0%, rgba(63,90,42,0) 38%),
      linear-gradient(180deg, #8a4636 0%, var(--brick) 60%, #4b4b4b 100%);
  }
</style>
</head>
<body>
  <section class="card card-front">
    <div class="band"></div>
    <div class="contact">
      <div class="person-name">DANIEL MERCER</div>
      <div class="person-title">Managing Director</div>
      <div class="contact-line">
        <svg viewBox="0 0 16 16" aria-hidden="true"><path fill="#f2b01e" d="M3 1h3l1.5 4-2 1.3a8 8 0 0 0 4.2 4.2L11 8.5l4 1.5v3a2 2 0 0 1-2 2A12 12 0 0 1 1 3a2 2 0 0 1 2-2z"/></svg>
        <span>914-555-0173</span>
      </div>
      <div class="contact-line">
        <svg viewBox="0 0 16 16" aria-hidden="true"><rect x="1" y="3" width="14" height="10" fill="#f2b01e"/><path d="M1 3l7 6 7-6" fill="none" stroke="#2b2b2b" stroke-width="1.4"/></svg>
        <span>mavreld@quintmail.com</span>
      </div>
    </div>
    <div class="divider"></div>
    <div class="brand">
      <div class="brand-mark">
        <span class="brand-dot"></span>
        <span class="brand-name">MAPLE 7 ON 2 HDFC</span>
      </div>
      <div class="address">4738 Larkwell Ave<br>Harlow Falls NY 12987</div>
    </div>
    <div class="slogan">TOGETHER WE ARE HOME</div>
  </section>

  <section class="card card-back">
    <div class="building-photo" role="img" aria-label="Photograph of the brick apartment building with fire escapes, trees and parked cars on the street"></div>
  </section>
</body>
</html>
```